Forensic Document Examiner, looking for contemporary update to my stationery design.

Looking for professional, classy logo design for stationery and business cards. My current stationery and business card is attached.I believe a logo image makes a header section interesting, so an intriguing design of a pen, feathered pen, microscope, magnifying glass, etc., would be appropriate. I have been in the business for over 30 years. I leave ideas to the imagination of the designer.My work involves mainly, the comparison of signatures and handwriting. I also resolve alterations, obliterations, and work as shown on my website: www.documentexaminer.infoThe image produced will be printed on quality white stationery and envelopes. The stationery will be photocopied by my clients, so the images should be reproducible. The business cards may be designed in other than white.

Target Market(s)

Attorneys

Font styles to use
Sans Serif

Colors

Designer to choose colors to be used in the design.

Requirements
Must have
• Image suitable for white stationery and photocopying.
• Classy logo and image; no casual fonts.
Nice to have
• Intriguing, contemporary design incorporating a relevant logo to my work.

```html
<!DOCTYPE html>
<html lang="en">
<head>
<meta charset="utf-8">
<title>Daniel R. Hale – Letterhead</title>
<link href="https://fonts.googleapis.com/css2?family=Crimson+Text:ital,wght@0,400;0,700;1,400&display=swap" rel="stylesheet">
<style>
  :root {
    --backdrop: #d9dcde;
    --paper: #ffffff;
    --navy: #2b2a6b;
    --ink-soft: #5a5a72;
    --rule: #b9bac6;
    --mark: #c9cad3;
  }
  * { box-sizing: border-box; margin: 0; padding: 0; }
  html, body {
    width: 1200px; height: 784px; overflow: hidden;
    background: var(--backdrop);
  }
  .canvas {
    width: 1200px; height: 784px;
    display: flex; align-items: center; justify-content: center;
  }
  .letterhead {
    position: relative;
    width: 572px; height: 740px;
    background: var(--paper);
    border-top: 5px solid var(--navy);
    box-shadow: 0 2px 10px rgba(0,0,0,0.12);
    font-family: "Crimson Text", Georgia, serif;
  }
  .identity {
    position: absolute; top: 30px; left: 34px;
    display: flex; align-items: center; gap: 10px;
  }
  .identity-dot {
    width: 34px; height: 34px; border-radius: 50%;
    background: var(--mark);
    flex: none;
  }
  .identity-name {
    font-size: 22px; font-weight: 700; color: var(--navy);
    line-height: 1;
  }
  .identity-title {
    font-size: 12px; font-style: italic; color: var(--ink-soft);
    margin-top: 4px; letter-spacing: 0.2px;
  }
  .contact {
    position: absolute; top: 300px; right: 26px;
    padding-left: 16px;
    border-left: 1px solid var(--rule);
    list-style: none;
  }
  .contact-item {
    display: flex; align-items: center; gap: 6px;
    font-size: 10.5px; font-style: italic; color: var(--navy);
    line-height: 1.55;
  }
  .contact-icon { width: 10px; height: 10px; flex: none; }
</style>
</head>
<body>
<main class="canvas">
  <article class="letterhead">
    <header class="identity">
      <span class="identity-dot"></span>
      <div>
        <div class="identity-name">Daniel R. Hale</div>
        <div class="identity-title">Forensic Document Examiner</div>
      </div>
    </header>

    <ul class="contact">
      <li class="contact-item">
        <svg class="contact-icon" viewBox="0 0 10 10"><circle cx="5" cy="5" r="5" fill="#2b2a6b"/><path d="M5 2.2a1.8 1.8 0 0 1 1.8 1.8C6.8 5.4 5 7.8 5 7.8S3.2 5.4 3.2 4A1.8 1.8 0 0 1 5 2.2z" fill="#fff"/></svg>
        PO Box 4182, Salem, OR 97301
      </li>
      <li class="contact-item">
        <svg class="contact-icon" viewBox="0 0 10 10"><circle cx="5" cy="5" r="5" fill="#2b2a6b"/><path d="M3.3 2.6l1 .9-.5.9c.4.8 1 1.4 1.8 1.8l.9-.5.9 1-.6.8C5.2 7.4 2.6 4.8 2.5 3.2z" fill="#fff"/></svg>
        555-214-0397
      </li>
      <li class="contact-item">
        <svg class="contact-icon" viewBox="0 0 10 10"><circle cx="5" cy="5" r="5" fill="#2b2a6b"/><rect x="2.5" y="3.3" width="5" height="3.4" fill="#fff"/><path d="M2.5 3.3L5 5.2l2.5-1.9" stroke="#2b2a6b" stroke-width=".6" fill="none"/></svg>
        dhale@quillmarkreview.info
      </li>
      <li class="contact-item">
        <svg class="contact-icon" viewBox="0 0 10 10"><circle cx="5" cy="5" r="5" fill="#2b2a6b"/><circle cx="5" cy="5" r="2.6" stroke="#fff" stroke-width=".6" fill="none"/><path d="M2.4 5h5.2M5 2.4c-1.2 1.4-1.2 3.8 0 5.2M5 2.4c1.2 1.4 1.2 3.8 0 5.2" stroke="#fff" stroke-width=".5" fill="none"/></svg>
        www.quillmarkreview.info
      </li>
    </ul>
  </article>
</main>
</body>
</html>
```